movie poster Dustwhisper

Create a movie poster for a thriller/suspense/horror movie called Dustwhisper which is about a monastery of sinister monks who are hell bent on destroying the world when three friends come on a photography assignment and find they may never escape!

A Marlene Hobart Film

Luke Penrose -- Owen
Danielle Forde -- Nora
Howard Pike -- Felix
Dale Ruddock --- Brother Lorenzo
Thaddeus Hobart -- Brother Benedetto
Norman Ellery ---Father Ignacio
Benjamin Holt -- Cardinal Vescovini
with Warren Tesky --- Gas Station Attendant

Marlene Hobart -- Writer, Director, Producer
Stephen Pike -- Director of Photography
Howard Pike -- Special Effects
Stephen Pike -- Editor
Lonnie "Buzzy" Marquez -- Sound

I just posted an update on the brief for the poster. Please include the credits on your movie poster. Thanks! I will be making a selection in the next few days.

Target Market(s)

This will be a PG and should attract a wide audience

Industry/Entity Type

Movie

Colors
eb1f27

Requirements
Must have
• Movie title, movie credits as provided
All material must be original --- no clip art or material taken from the internet
Nice to have
• tagline
Seeing is believing . . . until you believe what you don't see.

```html
<!DOCTYPE html>
<html lang="en">
<head>
<meta charset="utf-8">
<title>Dustwhisper — Movie Poster</title>
<link rel="stylesheet" href="https://fonts.googleapis.com/css2?family=Creepster&family=Oswald:wght@400;500;600&family=Kalam:wght@400&display=swap">
<style>
  :root {
    --blood: #eb1f27;
    --blood-deep: #7a0c10;
    --shadow: #140506;
    --ink: #ffffff;
    --ink-soft: #f3eaea;
  }
  html, body {
    margin: 0;
    padding: 0;
    overflow: hidden;
    background: var(--shadow);
  }
  .poster {
    position: relative;
    width: 810px;
    height: 1200px;
    overflow: hidden;
    background: var(--shadow);
  }
  .poster-art {
    position: absolute;
    inset: 0;
    background:
      radial-gradient(ellipse 30% 55% at 46% 48%, rgba(20,5,6,0.92) 0%, rgba(20,5,6,0.75) 55%, rgba(20,5,6,0) 100%),
      radial-gradient(ellipse 60% 40% at 80% 30%, rgba(255,255,255,0.35) 0%, rgba(255,255,255,0) 70%),
      radial-gradient(ellipse 70% 60% at 20% 40%, var(--blood) 0%, rgba(235,31,39,0) 75%),
      linear-gradient(180deg, var(--blood-deep) 0%, #b3161d 35%, #9b1218 65%, #3a0a0c 100%);
  }
  .cast {
    position: absolute;
    left: 0;
    right: 0;
    top: 288px;
    margin: 0;
    padding: 0;
    list-style: none;
    font-family: "Kalam", cursive;
    font-size: 36px;
    color: var(--ink);
    text-align: center;
    text-shadow: 2px 2px 0 var(--shadow), -1px -1px 0 var(--shadow), 1px -1px 0 var(--shadow), -1px 1px 0 var(--shadow);
  }
  .cast-row {
    display: flex;
    justify-content: center;
    gap: 30px;
    height: 78px;
    line-height: 52px;
  }
  .presenter {
    position: absolute;
    top: 666px;
    left: 0;
    right: 0;
    text-align: center;
    font-family: "Oswald", sans-serif;
    font-weight: 500;
    font-size: 27px;
    color: var(--ink);
    letter-spacing: 0.5px;
    margin: 0;
  }
  .presenter .small { font-size: 21px; }
  .title {
    position: absolute;
    top: 706px;
    left: 0;
    right: 0;
    margin: 0;
    text-align: center;
    font-family: "Creepster", cursive;
    font-weight: 400;
    font-size: 150px;
    line-height: 160px;
    letter-spacing: 2px;
    color: var(--ink-soft);
    text-transform: uppercase;
  }
  .tagline {
    position: absolute;
    top: 906px;
    left: 0;
    right: 0;
    margin: 0;
    text-align: center;
    font-family: "Oswald", sans-serif;
    font-weight: 600;
    font-size: 28px;
    color: var(--ink);
    font-variant: small-caps;
    letter-spacing: 1px;
  }
  .credits {
    position: absolute;
    left: 0;
    right: 0;
    top: 1076px;
    margin: 0;
    font-family: "Oswald", sans-serif;
    color: var(--ink);
  }
  .credits-row {
    display: flex;
    justify-content: center;
    align-items: center;
    gap: 22px;
    height: 60px;
  }
  .credit {
    display: flex;
    align-items: center;
    gap: 8px;
  }
  .credit-role {
    font-size: 9px;
    line-height: 10px;
    text-transform: uppercase;
    font-weight: 500;
    text-align: right;
  }
  .credit-role.inline { font-size: 13px; line-height: 1; }
  .credit-name {
    font-size: 24px;
    text-transform: uppercase;
    letter-spacing: 0.3px;
  }
</style>
</head>
<body>
<main class="poster">
  <div class="poster-art" role="img" aria-label="Hooded cloaked figure standing against a blood-red splattered texture"></div>

  <ul class="cast">
    <li class="cast-row"><span>Luke Penrose</span><span>Danielle Forde</span><span>Howard Pike</span></li>
    <li class="cast-row"><span>Norman Ellery</span><span>Thaddeus Hobart</span></li>
    <li class="cast-row"><span>Dale Ruddock</span><span>Benjamin Holt</span></li>
    <li class="cast-row"><span>with Warren Tesky</span></li>
  </ul>

  <p class="presenter"><span class="small">A</span> MARLENE HOBART <span class="small">MOVIE</span></p>

  <h1 class="title">Dustwhisper</h1>

  <p class="tagline">Seeing is believing . . . until you believe what you don't see.</p>

  <div class="credits">
    <div class="credits-row">
      <div class="credit"><span class="credit-role">Writer<br>Director<br>Producer</span><span class="credit-name">Marlene Hobart</span></div>
      <div class="credit"><span class="credit-role">Director of<br>Photography</span><span class="credit-name">Stephen Pike</span></div>
      <div class="credit"><span class="credit-role">Special<br>Effects</span><span class="credit-name">Howard Pike</span></div>
    </div>
    <div class="credits-row">
      <div class="credit"><span class="credit-role inline">Editor</span><span class="credit-name">Stephen Pike</span></div>
      <div class="credit"><span class="credit-role inline">Sound</span><span class="credit-name">Lonnie "Buzzy" Marquez</span></div>
    </div>
  </div>
</main>
</body>
</html>
```